Moravel Ridge Wine Club-The Quiet Roster

We are a new aspirational brand of fine Tasmania Wine. We need a commitment club poster which appeals to the ego.We have one opportunity to get customers to sign up and that is when they visit at the cellar door. This club is the core of our business.

The brand is a clean, pure , simple brand, black and white very sophiscated.
This is a top end product.

Our Commitment Club is named The Quiet Roster which is a play on words. Tradionally The Quiet Roster is a list of people that you dont want to do business with. So we are turning this on its had.

You need to make this poster sharp, desirable, possibly sexy but masculine. Im thinking Victor Crane . It doesnt matter the client will be 40 up fashion consious looking for something new , exclusive , something there peers don't have.

I dont like busy! make it clean clear and basically undeniable. The client must not be able to resist the offer.

www.moravelridge.example.au

Target Market(s)

Appreciator 40-60 male wants to be recognised fashion consious sophiscated has money and wants to part of something exclusive.

A feeling that you are part of something that only a few are. Exclusive

Maybe an imagine of beautiful people 30/40ish I want to be drinking Moravel Wine / in The Quiet Roster

Industry/Entity Type

Fashion

Requirements
Must have
• Moravel Ridge Logo
MORAVEL Bottles images

We produce only 1600 cases of wine each vintage. Therefore we have limited membership 001-999 for our club.
Award Winning Wines available exclusively from us.

Gold Member
We will reserve 2 cases of our limited vintage, to be delivered to you in May and Oct.
Single varietal or mixed cases. You receive a 15% discount.

Silver Member
We will reserve 1 case of our limited vintage to be delivered to you 6 bottles in May and 6 in Oct.
Single varietal or mixed cases. You receive a 10% discount.

To you exclusively from us not, available from any other retailers.

You will be invited to Quiet Roster Only Events and Tastings.
You will get preferential access to new and limited releases.
Members will be entered in a bi annual draw to win a 2 night stay here at the Moravel Thornbury Cottage on the Freycinet Coast Tasmania.

Nice to have

Should not have
• VIP stamps,gimacs, anything that cheapens our brand.

We do not like busy posters please have white space

```html
<!DOCTYPE html>
<html lang="en">
<head>
<meta charset="utf-8">
<title>Moravel Ridge Wine Club – The Quiet Roster</title>
<link rel="stylesheet" href="https://fonts.googleapis.com/css2?family=Archivo+Black&family=Pinyon+Script&family=Questrial&display=swap">
<style>
  :root {
    --ink: #111111;
    --black: #050505;
    --cream: #e9e0cd;
    --cream-deep: #cbbd9f;
    --sand: #d8ccb2;
    --gold-light: #fbf1dc;
    --gold: #c9ad7e;
    --gold-deep: #8a6e45;
    --white: #ffffff;
    --brand: #1a1a1a;
  }
  * { box-sizing: border-box; margin: 0; padding: 0; }
  html, body { width: 960px; height: 1200px; overflow: hidden; background: var(--white); }
  .poster {
    position: relative;
    width: 960px;
    height: 1200px;
    overflow: hidden;
    font-family: "Questrial", "Helvetica Neue", Arial, sans-serif;
    color: var(--ink);
    background: var(--cream);
  }

  /* Hero */
  .hero {
    position: absolute; left: 0; top: 0; width: 960px; height: 461px;
    background: radial-gradient(ellipse at 50% 40%, #f1eadb 0%, #e4dac4 60%, #d3c6aa 100%);
  }
  .hero-photo {
    position: absolute; top: 0; height: 461px; width: 290px;
    background: linear-gradient(180deg, #3a3630 0%, #1d1b18 55%, #2b2824 100%);
  }
  .hero-photo--left { left: 0; }
  .hero-photo--right { right: 0; }
  .brand {
    position: absolute; left: 0; right: 0; top: 110px;
    text-align: center;
    font-family: "Questrial", "Helvetica Neue", Arial, sans-serif;
    font-size: 70px; letter-spacing: 6px;
    color: var(--brand);
    line-height: 1;
  }
  .brand-sub {
    position: absolute; left: 0; right: 0; top: 192px;
    text-align: center;
    font-size: 26px; letter-spacing: 8px;
    color: var(--brand);
  }
  .hero-intro {
    position: absolute; left: 230px; right: 230px; top: 247px;
    text-align: center;
    font-size: 19px; line-height: 24px; letter-spacing: 0.5px;
    color: var(--white);
    text-shadow: 0 0 3px rgba(0,0,0,.7), 1px 1px 2px rgba(0,0,0,.6);
  }
  .entry-badge {
    position: absolute; left: 360px; top: 348px; width: 240px; height: 60px;
    display: flex; align-items: center; justify-content: center;
    font-size: 27px; color: var(--ink);
    background: linear-gradient(180deg, var(--gold-light) 0%, #e6d3ae 45%, var(--gold) 100%);
    border: 1px solid var(--gold-deep);
    border-radius: 3px;
    box-shadow: 0 2px 6px rgba(0,0,0,.35);
  }

  /* Roster band */
  .roster-band {
    position: absolute; left: 0; top: 461px; width: 960px; height: 192px;
    background: radial-gradient(ellipse at 50% 55%, #3a2a18 0%, var(--black) 45%);
    border-top: 6px solid var(--gold-deep);
    border-bottom: 6px solid var(--gold-deep);
    text-align: center;
  }
  .roster-title {
    margin-top: 22px;
    font-family: "Archivo Black", "Arial Black", sans-serif;
    font-size: 62px; line-height: 76px; letter-spacing: 1px;
    background: linear-gradient(180deg, #fff6e4 0%, #e5cfa5 45%, #a9895a 100%);
    -webkit-background-clip: text; background-clip: text;
    color: transparent;
  }
  .roster-perks {
    list-style: none;
    font-size: 25px; line-height: 32px;
    color: var(--white);
  }

  /* Offer */
  .offer {
    position: absolute; left: 0; top: 653px; width: 960px; height: 456px;
    background: radial-gradient(ellipse at 50% 70%, #f6f0e3 0%, var(--sand) 70%, var(--cream-deep) 100%);
  }
  .offer-script {
    position: absolute; left: 0; right: 0; top: 22px;
    text-align: center;
    font-family: "Pinyon Script", cursive;
    font-size: 84px; line-height: 100px;
    color: var(--ink);
  }
  .offer-exclusive {
    position: absolute; left: 0; right: 0; top: 138px;
    text-align: center;
    font-size: 25px; color: var(--ink);
  }
  .tier {
    position: absolute; top: 200px; width: 350px; text-align: center;
  }
  .tier--gold { left: 67px; }
  .tier--silver { left: 540px; }
  .tier-title {
    font-family: "Archivo Black", "Arial Black", sans-serif;
    font-size: 29px; letter-spacing: -0.5px; line-height: 40px;
    color: var(--ink);
    text-shadow: 1px 2px 2px rgba(0,0,0,.35);
    text-align: left; padding-left: 12px;
  }
  .tier--silver .tier-title { padding-left: 12px; }
  .tier-rule {
    height: 4px; width: 340px; background: var(--ink);
    margin: 4px 0 14px 0;
  }
  .tier-terms {
    list-style: none;
    font-size: 17px; line-height: 23px; color: var(--ink);
  }
  .tier-terms .discount { font-weight: 700; font-family: "Helvetica Neue", Arial, sans-serif; font-size: 16px; }

  .bottles {
    position: absolute; left: 413px; top: 950px; width: 140px; height: 250px;
    background: linear-gradient(90deg, #c9c06a 0%, #b7ae4f 28%, #5a0f16 36%, #7a1620 64%, #e79a84 72%, #f1b3a0 100%);
    border-radius: 10px 10px 0 0;
    z-index: 2;
  }

  /* Footer */
  .footer {
    position: absolute; left: 0; top: 1109px; width: 960px; height: 91px;
    background: var(--black);
    color: var(--white);
    font-size: 13px; line-height: 16px;
  }
  .footer-address { position: absolute; left: 67px; top: 22px; font-style: normal; }
  .footer-contact { position: absolute; right: 67px; top: 38px; text-align: right; }
</style>
</head>
<body>
<main class="poster">
  <section class="hero">
    <div class="hero-photo hero-photo--left" role="img" aria-label="Photograph of a waiter in a tuxedo holding a silver tray with a glass of red wine"></div>
    <div class="hero-photo hero-photo--right" role="img" aria-label="Photograph of a waiter in a tuxedo holding a silver tray with a glass of red wine"></div>
    <h1 class="brand">Moravel</h1>
    <p class="brand-sub">RIDGE</p>
    <p class="hero-intro">We want you to become part of our story. Join the Moravel Wine Club to get the most out of the wines you love.</p>
    <div class="entry-badge">LIMITED ENTRY</div>
  </section>

  <section class="roster-band">
    <h2 class="roster-title">JOIN THE QUIET ROSTER</h2>
    <ul class="roster-perks">
      <li>VIP Access to Quiet Roster Only Tastings and Events</li>
      <li>Preferential Access to First Releases and Limited Releases</li>
    </ul>
  </section>

  <section class="offer">
    <h2 class="offer-script">Fine Tasmania Wine</h2>
    <p class="offer-exclusive">Exclusively To You, From Us. Not Available by Other Retailers.</p>

    <article class="tier tier--gold">
      <h3 class="tier-title">GOLD MEMBERSHIP</h3>
      <div class="tier-rule"></div>
      <ul class="tier-terms">
        <li>Reserve 2 Cases of Vintage Wine</li>
        <li>Delivered Directly to You</li>
        <li>One Case in May, One Case in October</li>
        <li>You Choose the Variety of Wine</li>
        <li class="discount">Receive a 15% DISCOUNT</li>
      </ul>
    </article>

    <article class="tier tier--silver">
      <h3 class="tier-title">SILVER MEMBERSHIP</h3>
      <div class="tier-rule"></div>
      <ul class="tier-terms">
        <li>Reserve Two 1/2 cases of Vintage Wine</li>
        <li>Delivered Directly to You</li>
        <li>One Case in May, One Case in October</li>
        <li>You choose the Variety of Wine</li>
        <li class="discount">Receive a 10% DISCOUNT</li>
      </ul>
    </article>
  </section>

  <div class="bottles" role="img" aria-label="Photograph of three Moravel wine bottles: white, red and rosé"></div>

  <footer class="footer">
    <address class="footer-address">
      Moravel Ridge<br>
      Cellar Door: 2207 Ferncliff Road<br>
      Lowmoor Tasmania 7999
    </address>
    <p class="footer-contact">
      www.moravelridge.example.au<br>
      Telephone: 0400 555 018 / 0400 555 094
    </p>
  </footer>
</main>
</body>
</html>
```